Business Card Design Project

Business Card
We are rebranding with a new logo
Industry/Entity Type
Business
Contact Information for Business Card
Dennis Morvale +61 487215963 dennis@quorv.com.au P.O. Box 872 Fernlow QLD 4309
Requirements
Must have
- Logo

```html
<!DOCTYPE html>
<html lang="en">
<head>
<meta charset="utf-8">
<title>Quorv International – Business Card</title>
<link rel="stylesheet" href="https://fonts.googleapis.com/css2?family=Courgette&family=Roboto:wght@400;700&display=swap">
<style>
  :root {
    --backdrop: #e8e8e8;
    --blue-deep: #0b4d70;
    --blue-mid: #0a7fb6;
    --blue-bright: #05a3de;
    --card-white: #f7f7f7;
    --ink: #1d1d1f;
    --name-ink: #0b4d70;
    --white: #ffffff;
    --icon: #f08a1c;
  }
  * { box-sizing: border-box; margin: 0; padding: 0; }
  html, body {
    width: 1200px; height: 576px; overflow: hidden;
    background: var(--backdrop);
    font-family: "Roboto", Arial, sans-serif;
  }
  .canvas { position: relative; width: 1200px; height: 576px; }
  .card {
    position: absolute; top: 139px;
    width: 482px; height: 290px;
    border-radius: 12px; overflow: hidden;
  }
  .card-front {
    left: 82px;
    background: linear-gradient(90deg, var(--blue-deep) 0%, var(--blue-mid) 50%, var(--blue-bright) 100%);
  }
  .card-back { left: 602px; background: var(--card-white); }

  .brand {
    position: absolute;
    font-family: "Roboto", Arial, sans-serif;
    font-weight: 700;
    line-height: 1;
  }
  .brand-word { display: block; font-size: 52px; letter-spacing: 1px; }
  .brand-tag { display: block; font-size: 17px; letter-spacing: 3px; margin-top: 8px; }
  .card-front .brand { left: 152px; top: 100px; color: var(--white); }
  .card-back .brand { left: 48px; top: 88px; color: var(--blue-deep); }

  .decor-band {
    position: absolute; left: 0; right: 0; top: 196px; bottom: 0;
    background: linear-gradient(90deg, var(--blue-bright) 0%, var(--blue-mid) 45%, var(--blue-deep) 100%);
  }

  .person { position: absolute; right: 20px; top: 42px; text-align: right; }
  .person-name {
    font-family: "Courgette", cursive;
    font-size: 26px; color: var(--name-ink); line-height: 1;
  }
  .person-role { font-size: 11.5px; color: var(--ink); margin-top: 8px; }

  .contact {
    position: absolute; right: 18px; top: 222px;
    list-style: none; text-align: right;
  }
  .contact li {
    display: flex; justify-content: flex-end; align-items: center;
    gap: 8px; font-size: 12px; color: var(--white);
    height: 17px;
  }
  .contact svg { width: 11px; height: 11px; fill: var(--icon); flex: none; }
</style>
</head>
<body>
<main class="canvas">
  <section class="card card-front" aria-label="Card front">
    <div class="brand">
      <span class="brand-word">Quorv</span>
      <span class="brand-tag">INTERNATIONAL</span>
    </div>
  </section>

  <section class="card card-back" aria-label="Card back">
    <div class="decor-band" role="img" aria-label="Orange and blue wave decoration across the lower card"></div>

    <div class="brand">
      <span class="brand-word">Quorv</span>
      <span class="brand-tag">INTERNATIONAL</span>
    </div>

    <div class="person">
      <p class="person-name">Dennis Morvale</p>
      <p class="person-role">Managing Director</p>
    </div>

    <ul class="contact">
      <li>+61 487215963
        <svg viewBox="0 0 24 24" aria-hidden="true"><path d="M6.6 10.8a15.1 15.1 0 0 0 6.6 6.6l2.2-2.2a1 1 0 0 1 1-.25 11.4 11.4 0 0 0 3.6.57 1 1 0 0 1 1 1V20a1 1 0 0 1-1 1A17 17 0 0 1 3 4a1 1 0 0 1 1-1h3.5a1 1 0 0 1 1 1c0 1.25.2 2.45.57 3.57a1 1 0 0 1-.25 1z"/></svg>
      </li>
      <li>dennis@quorv.com.au
        <svg viewBox="0 0 24 24" aria-hidden="true"><path d="M2 5h20v14H2z M2 5l10 8 10-8" stroke="var(--blue-deep)" stroke-width="1.5"/></svg>
      </li>
      <li>P.O. Box 872 Fernlow QLD 4309
        <svg viewBox="0 0 24 24" aria-hidden="true"><path d="M12 2a7 7 0 0 0-7 7c0 5.2 7 13 7 13s7-7.8 7-13a7 7 0 0 0-7-7zm0 9.5A2.5 2.5 0 1 1 12 6.5a2.5 2.5 0 0 1 0 5z"/></svg>
      </li>
    </ul>
  </section>
</main>
</body>
</html>
```